uk based ecommerce website requires fresh look ,high quality look and feel

we are a web based company selling eco friendly ground reinforcement grids to diy and construction sectors
our existing website is www.pondermeshpaths.co.uk ,

we have already updated the logo so that is the branding sorted .so we need a ecommerce website that is very much up-to date in design and layout and which has content management system for ease of use so that we can add products and information as required.

Use current logo as reference for colour scheme.
www.pondermeshpaths.co.uk

The current website has 6 pages accessible through the navigation bar, I would now like 5 pages, removing the need for the Trade Enquiries page possibly have it with along with contact us.

Target Market(s)

construction industry , diy end users,
retail market, landscapers, gardeners

Industry/Entity Type

Construction

Font styles to use
Other font styles liked:
• logo font prometo

Colors
f78f20
9bcb3c

Requirements
Must have
• logo colours and logo design in website with cms responsive design for tablet and mobile devices
• expect content to work flawlessly and look great across all devices
• HTML 5 custom design with coding as required
• must have good experiance in ecommerce website design
• eye catching, high quality look and feel and very user friedly ,very up-to date.
Nice to have
• picture slider show
• explain in writing what exactly i am getting in my ecommerce website
Should not have
• plain , basic design , old fashion looking ,cheap look

```html
<!DOCTYPE html>
<html lang="en">
<head>
<meta charset="utf-8">
<title>Pondermesh Ground Solutions</title>
<link rel="stylesheet" href="https://fonts.googleapis.com/css2?family=Open+Sans:wght@400;600;700;800&display=swap">
<style>
:root{
  --orange:#f78f20;
  --green:#9bcb3c;
  --dark:#333333;
  --text:#444444;
  --muted:#777777;
  --line:#e2e2e2;
  --footer:#ebebeb;
  --white:#ffffff;
}
*{box-sizing:border-box;margin:0;padding:0}
html,body{width:1200px;height:2711px;overflow:hidden}
body{position:relative;background:var(--white);font-family:"Open Sans",Arial,sans-serif;color:var(--text)}
.abs{position:absolute}

/* top bar */
.topbar{left:0;top:0;width:1200px;height:40px;background:var(--white)}
.topbar-strip{left:650px;top:0;width:450px;height:40px;background:var(--orange);display:flex;align-items:center;font-size:14px;color:var(--white);font-weight:600}
.topbar-phone{display:flex;align-items:center;gap:7px;padding:0 22px 0 24px}
.topbar-link{display:flex;align-items:center;gap:6px;height:40px;padding:0 14px;font-size:12px;text-transform:uppercase}
.topbar-link.login{background:var(--green)}
.topbar-cart{margin-left:auto;height:40px;background:var(--green);padding:4px 14px;font-size:12px;line-height:15px;text-transform:uppercase;display:flex;align-items:center;gap:6px}
.topbar-cart small{display:block;font-size:10px;text-transform:none;font-weight:400}

/* header */
.brand{left:99px;top:48px;display:flex;align-items:center;gap:14px}
.brand-mark{width:64px;height:64px;border-radius:50%;background:var(--green)}
.brand-name{font-size:31px;font-weight:800;color:var(--orange);line-height:34px;letter-spacing:.5px}
.brand-name span{display:block;font-size:17px;line-height:22px;font-weight:800;color:var(--orange)}
.search{left:674px;top:67px;width:230px;height:30px;display:flex;border:1px solid var(--line)}
.search input{flex:1;border:0;padding:0 10px;font-family:inherit;font-size:11px;color:var(--muted)}
.search-btn{width:34px;background:var(--orange);display:flex;align-items:center;justify-content:center}
.messaging{left:935px;top:68px;display:flex;align-items:center;gap:10px;font-size:10px;color:var(--dark);line-height:13px;text-transform:uppercase}
.messaging b{display:block;font-size:11px}
.nav{right:100px;top:128px;display:flex;font-size:13px;font-weight:600;text-transform:uppercase;color:var(--dark)}
.nav a{color:inherit;text-decoration:none;padding:0 18px;border-left:1px solid #cfcfcf;line-height:16px}
.nav a:first-child{border-left:0}
.nav a:last-child{padding-right:0}
.nav a.active{color:var(--orange)}

/* hero */
.hero{left:99px;top:173px;width:1001px;height:393px;overflow:hidden;background:linear-gradient(180deg,#b7c3c9 0%,#9aa38a 35%,#c9bfae 65%,#d8d1c2 100%)}
.hero-caption{left:380px;top:455px;width:688px;text-align:right;font-size:25px;line-height:36px;font-weight:700;color:var(--white);text-shadow:0 2px 4px rgba(0,0,0,.45);white-space:nowrap}
.hero-arrow{top:352px;width:38px;height:38px;background:rgba(40,40,40,.8);display:flex;align-items:center;justify-content:center}

/* section titles */
.section-title{left:0;width:1200px;text-align:center;font-size:30px;line-height:40px;font-weight:700;color:var(--dark);text-transform:uppercase}
.section-title em{font-style:normal;color:var(--orange)}
.section-rule{left:362px;width:476px;height:2px;background:var(--line)}
.section-rule::after{content:"";position:absolute;left:193px;top:0;width:90px;height:2px;background:var(--orange)}

/* categories */
.category{width:315px;height:180px;overflow:hidden}
.category-label{position:absolute;left:0;bottom:0;width:100%;height:34px;background:rgba(25,25,25,.72);color:var(--white);font-size:12px;font-weight:700;text-transform:uppercase;padding:0 12px;line-height:34px;letter-spacing:.3px}
.carousel-track{left:175px;top:1130px;width:855px;height:1px;background:var(--line)}
.carousel-track .fill{position:absolute;left:450px;top:0;width:405px;height:2px;background:var(--green)}
.dot{top:1117px;width:26px;height:26px;border-radius:50%;display:flex;align-items:center;justify-content:center}

/* sidebar */
.side-box{left:99px;width:214px;text-align:center;color:var(--white)}
.side-box h3{font-size:19px;font-weight:700;line-height:24px}
.pdf-btn{display:inline-block;background:var(--white);color:var(--dark);font-size:15px;padding:5px 12px;border:1px solid #ddd}
.side-photo{margin:10px auto 0;width:190px;height:106px;border:4px solid var(--white)}

/* featured */
.featured-bar{left:336px;top:1193px;width:764px;height:38px;background:var(--green);color:var(--white);font-size:17px;font-weight:700;line-height:38px;padding-left:14px;text-transform:uppercase}
.featured-notch{left:1080px;top:1193px}
.product{width:246px;height:320px;border:1px solid var(--line);text-align:center}
.product-photo{position:absolute;left:11px;top:11px;width:222px;height:172px}
.sale{position:absolute;right:8px;top:0;background:var(--green);color:var(--white);font-size:11px;font-weight:700;padding:2px 7px}
.price{position:absolute;left:0;top:198px;width:100%;font-size:18px;font-weight:700;color:var(--orange)}
.product-name{position:absolute;left:12px;top:228px;width:220px;font-size:12px;line-height:18px;color:var(--dark)}
.cart-btn{position:absolute;left:62px;top:276px;display:flex;height:30px}
.cart-btn span{background:var(--dark);color:var(--white);font-size:11px;font-weight:700;padding:0 10px;line-height:30px}
.cart-btn i{width:34px;background:var(--orange);clip-path:polygon(0 0,75% 0,100% 50%,75% 100%,0 100%);display:flex;align-items:center;justify-content:center}

/* gallery */
.tile{overflow:hidden}
.tile-overlay{position:absolute;inset:0;background:rgba(60,60,60,.75);display:flex;flex-direction:column;align-items:center;justify-content:center;color:var(--white);font-size:18px;font-weight:700;line-height:24px;text-align:center}
.gal-arrow{top:2180px;width:32px;height:32px;border-radius:50%;border:1px solid #bbb;display:flex;align-items:center;justify-content:center;background:var(--white)}

/* footer */
.footer{left:0;top:2403px;width:1200px;height:257px;background:var(--footer);border-top:3px solid #d6d6d6}
.footer h4{font-size:18px;font-weight:700;color:var(--dark);margin-bottom:18px}
.quick-links{list-style:none;font-size:12px;color:var(--dark);line-height:28px}
.quick-links li::before{content:"›";color:var(--orange);margin-right:10px}
.contact-line{display:flex;gap:12px;font-size:12px;line-height:17px;color:var(--dark);margin-bottom:12px}
.contact-line svg{flex:none;margin-top:2px}
.map{width:248px;height:134px;background:linear-gradient(135deg,#d6e3ee 0%,#c8d8b8 45%,#e6e1d4 100%);border:3px solid var(--white)}
.footer-brand{display:flex;align-items:center;gap:10px}
.footer-brand .brand-mark{width:50px;height:50px}
.footer-brand div{font-size:22px;font-weight:800;color:var(--orange);line-height:25px}
.footer-brand div span{display:block;font-size:13px;line-height:17px}
.social{display:flex;gap:8px}
.social i{width:27px;height:27px;border-radius:50%;background:var(--dark);display:block}
.copyright{left:0;top:2660px;width:1200px;height:51px;background:var(--orange);color:var(--white);font-size:11px;line-height:51px;padding-left:99px;text-transform:uppercase}
.pay{top:2673px;width:42px;height:26px;background:var(--white);border-radius:2px}
</style>
</head>
<body>

<!-- top bar -->
<div class="abs topbar"></div>
<div class="abs topbar-strip">
  <div class="topbar-phone">
    <svg width="18" height="18" viewBox="0 0 18 18"><circle cx="9" cy="9" r="8" fill="none" stroke="#fff" stroke-width="1.6"/><path d="M6 5.5l1.6-.5 1 2-1 .8c.5 1.1 1.2 1.8 2.3 2.3l.8-1 2 1-.5 1.6c-3 .3-6.5-3.2-6.2-6.2z" fill="#fff"/></svg>
    0131-555-0182
  </div>
  <div class="topbar-link login">
    <svg width="12" height="13" viewBox="0 0 12 13"><rect x="1" y="6" width="10" height="7" fill="#fff"/><path d="M3 6V4a3 3 0 016 0v2" fill="none" stroke="#fff" stroke-width="1.6"/></svg>Login
  </div>
  <div class="topbar-link">
    <svg width="13" height="13" viewBox="0 0 13 13"><rect x="1" y="2" width="10" height="10" fill="none" stroke="#fff" stroke-width="1.4"/><path d="M5 8l6-6" stroke="#fff" stroke-width="1.6"/></svg>Sign Up
  </div>
  <div class="topbar-cart">
    <svg width="20" height="18" viewBox="0 0 20 18"><path d="M1 2h3l2 9h10l2-7H5" fill="none" stroke="#fff" stroke-width="1.6"/><circle cx="8" cy="15" r="1.6" fill="#fff"/><circle cx="15" cy="15" r="1.6" fill="#fff"/></svg>
    <div>Cart<small>(empty)</small></div>
  </div>
</div>

<!-- header -->
<div class="abs brand">
  <div class="brand-mark"></div>
  <div class="brand-name">PONDERMESH<span>GROUND SOLUTIONS</span></div>
</div>
<div class="abs search">
  <input type="text" value="Enter product name" aria-label="Search products">
  <div class="search-btn"><svg width="15" height="15" viewBox="0 0 15 15"><circle cx="6" cy="6" r="4.5" fill="none" stroke="#fff" stroke-width="2"/><path d="M9.5 9.5l4 4" stroke="#fff" stroke-width="2"/></svg></div>
</div>
<div class="abs messaging">
  <svg width="24" height="18" viewBox="0 0 24 18"><rect x="1" y="1" width="22" height="16" fill="none" stroke="var(--green)" stroke-width="2"/><path d="M1 1l11 9 11-9" fill="none" stroke="var(--green)" stroke-width="2"/></svg>
  <div>24/7 Hour<b>Messaging Service</b></div>
</div>
<nav class="abs nav">
  <a class="active" href="#">Home</a><a href="#">About Us</a><a href="#">Ground Solutions</a><a href="#">Pondermesh</a><a href="#">Contact Us</a>
</nav>

<!-- hero slider -->
<div class="abs hero" role="img" aria-label="Photo of a gravel driveway laid with reinforcement grid beside a house"></div>
<div class="abs hero-caption">We Provide Quality Products At An Affordable Price &amp;<br>Which Meets The Requirements Of Our Customers.</div>
<div class="abs hero-arrow" style="left:99px"><svg width="12" height="14" viewBox="0 0 12 14"><path d="M9 1L3 7l6 6" fill="none" stroke="#fff" stroke-width="2.4"/></svg></div>
<div class="abs hero-arrow" style="left:1062px"><svg width="12" height="14" viewBox="0 0 12 14"><path d="M3 1l6 6-6 6" fill="none" stroke="#fff" stroke-width="2.4"/></svg></div>

<!-- categories -->
<h2 class="abs section-title" style="top:610px"><em>Shop By</em> Product Category</h2>
<div class="abs section-rule" style="top:662px"></div>

<div class="abs category" style="left:99px;top:701px;background:linear-gradient(160deg,#8a8b7e,#4a4d4c)" role="img" aria-label="Geotextile membrane laid on a prepared base"><div class="category-label">Geotextile Membranes</div></div>
<div class="abs category" style="left:443px;top:701px;background:linear-gradient(160deg,#6e6e6e,#2f2f2f)" role="img" aria-label="Gravel filled hexagonal grid for light driveways"><div class="category-label">Light Domestic Driveways</div></div>
<div class="abs category" style="left:784px;top:701px;background:linear-gradient(160deg,#9a9d9c,#d8d4cb)" role="img" aria-label="Car parked on a gravel heavy duty driveway"><div class="category-label">Heavy Domestic Driveways</div></div>
<div class="abs category" style="left:99px;top:904px;background:linear-gradient(160deg,#a7a69e,#555)" role="img" aria-label="Workers laying grids for a commercial car park"><div class="category-label">Commercial Parking System</div></div>
<div class="abs category" style="left:443px;top:904px;background:linear-gradient(160deg,#7c6e5e,#c9a985)" role="img" aria-label="Grid pathway installation with a vehicle"><div class="category-label">Parking &amp; Pathway Systems</div></div>
<div class="abs category" style="left:784px;top:904px;background:linear-gradient(180deg,#8fa9a0,#56743c 55%,#c8b592)" role="img" aria-label="Equestrian arena on grid surface"><div class="category-label">Equestrian Grid</div></div>

<div class="abs carousel-track"><div class="fill"></div></div>
<div class="abs dot" style="left:576px;background:#ddd"><svg width="8" height="10" viewBox="0 0 8 10"><path d="M6 1L2 5l4 4" fill="none" stroke="#777" stroke-width="1.8"/></svg></div>
<div class="abs dot" style="left:612px;background:var(--green)"><svg width="8" height="10" viewBox="0 0 8 10"><path d="M2 1l4 4-4 4" fill="none" stroke="#fff" stroke-width="1.8"/></svg></div>

<!-- sidebar -->
<div class="abs side-box" style="top:1193px;height:206px;background:var(--orange);padding-top:1px">
  <div class="side-photo" style="background:linear-gradient(90deg,#c9b98e,#bfc4c2)" role="img" aria-label="Gravel in a white hexagonal grid"></div>
  <h3 style="margin-top:10px">PONDERMESH 25</h3>
  <span class="pdf-btn" style="margin-top:8px">Download PDF</span>
</div>
<div class="abs side-box" style="top:1422px;height:213px;background:#4a4a4a;padding-top:42px">
  <svg width="74" height="46" viewBox="0 0 74 46"><rect x="2" y="4" width="44" height="28" fill="#fff"/><path d="M46 12h14l10 11v9H46z" fill="#fff"/><circle cx="16" cy="36" r="6" fill="#fff" stroke="#4a4a4a" stroke-width="3"/><circle cx="58" cy="36" r="6" fill="#fff" stroke="#4a4a4a" stroke-width="3"/><text x="8" y="24" font-family="Open Sans, sans-serif" font-size="12" font-weight="800" fill="#4a4a4a">FREE</text></svg>
  <h3 style="font-size:26px;line-height:34px;margin-top:8px">Free Shipping</h3>
  <div style="font-size:15px;margin-top:6px">Orders Over £ 100</div>
</div>
<div class="abs side-box" style="top:1657px;height:246px;background:var(--green);padding-top:1px">
  <div class="side-photo" style="background:linear-gradient(90deg,#222,#eee)" role="img" aria-label="Black and white gravel grid panels"></div>
  <h3 style="margin-top:10px">Gravel Grid Data<br>Sheet</h3>
  <span class="pdf-btn" style="margin-top:10px">Download PDF</span>
</div>

<!-- featured products -->
<div class="abs featured-bar">Featured Products</div>
<svg class="abs featured-notch" width="20" height="38" viewBox="0 0 20 38"><path d="M0 0h20L8 19l12 19H0z" fill="var(--green)"/></svg>

<div class="abs product" style="left:336px;top:1243px">
  <div class="product-photo" style="background:linear-gradient(160deg,#555,#8a8a8a)" role="img" aria-label="Bicycle wheel on gravel grid"></div>
  <div class="price">£ 11.00</div><div class="product-name">Pondermesh 25<br>System</div>
  <div class="cart-btn"><span>Add To Cart</span><i><svg width="12" height="11" viewBox="0 0 12 11"><path d="M1 1h2l1.5 6h6l1-4H4" fill="none" stroke="#fff" stroke-width="1.4"/></svg></i></div>
</div>
<div class="abs product" style="left:593px;top:1243px">
  <div class="product-photo" style="background:linear-gradient(160deg,#8a8a8a,#bdb7ab)" role="img" aria-label="Lorry wheels on paving grid"></div><div class="sale">SALE</div>
  <div class="price">£ 9.58</div><div class="product-name">Terragrid 40 Paving<br>System For Grass &amp; Gravel</div>
  <div class="cart-btn"><span>Add To Cart</span><i><svg width="12" height="11" viewBox="0 0 12 11"><path d="M1 1h2l1.5 6h6l1-4H4" fill="none" stroke="#fff" stroke-width="1.4"/></svg></i></div>
</div>
<div class="abs product" style="left:849px;top:1243px">
  <div class="product-photo" style="background:linear-gradient(160deg,#5c6b4d,#8c7a66)" role="img" aria-label="Steel U pin holding mesh on grass"></div>
  <div class="price">£ 37.50</div><div class="product-name">Steel U Pins</div>
  <div class="cart-btn"><span>Add To Cart</span><i><svg width="12" height="11" viewBox="0 0 12 11"><path d="M1 1h2l1.5 6h6l1-4H4" fill="none" stroke="#fff" stroke-width="1.4"/></svg></i></div>
</div>
<div class="abs product" style="left:336px;top:1585px">
  <div class="product-photo" style="background:linear-gradient(160deg,#6f8f3b,#a9c46a)" role="img" aria-label="Green turf reinforcement mesh"></div><div class="sale">SALE</div>
  <div class="price">£ 155.00</div><div class="product-name">Turf Reinforcement Mesh 2 Tonne<br>Loading Per Sq M2</div>
  <div class="cart-btn"><span>Add To Cart</span><i><svg width="12" height="11" viewBox="0 0 12 11"><path d="M1 1h2l1.5 6h6l1-4H4" fill="none" stroke="#fff" stroke-width="1.4"/></svg></i></div>
</div>
<div class="abs product" style="left:593px;top:1585px">
  <div class="product-photo" style="background:linear-gradient(160deg,#bfc2c4,#e6e7e8)" role="img" aria-label="White hexagonal parking grid panels"></div>
  <div class="price">£ 12.50</div><div class="product-name">Hexbase 30 Parking &amp; Pathway<br>System In White</div>
  <div class="cart-btn"><span>Add To Cart</span><i><svg width="12" height="11" viewBox="0 0 12 11"><path d="M1 1h2l1.5 6h6l1-4H4" fill="none" stroke="#fff" stroke-width="1.4"/></svg></i></div>
</div>
<div class="abs product" style="left:849px;top:1585px">
  <div class="product-photo" style="background:linear-gradient(160deg,#7ea046,#d9dcd2)" role="img" aria-label="White edging corner piece on grass"></div><div class="sale">SALE</div>
  <div class="price">£ 23.33</div><div class="product-name">External Corner Pack</div>
  <div class="cart-btn"><span>Add To Cart</span><i><svg width="12" height="11" viewBox="0 0 12 11"><path d="M1 1h2l1.5 6h6l1-4H4" fill="none" stroke="#fff" stroke-width="1.4"/></svg></i></div>
</div>

<!-- project gallery -->
<h2 class="abs section-title" style="top:1958px"><em>Project</em> Gallery</h2>
<div class="abs section-rule" style="top:2010px"></div>

<div class="abs gal-arrow" style="left:47px"><svg width="8" height="12" viewBox="0 0 8 12"><path d="M6 1L2 6l4 5" fill="none" stroke="#999" stroke-width="1.6"/></svg></div>
<div class="abs gal-arrow" style="left:1120px"><svg width="8" height="12" viewBox="0 0 8 12"><path d="M2 1l4 5-4 5" fill="none" stroke="#999" stroke-width="1.6"/></svg></div>

<div class="abs tile" style="left:99px;top:2042px;width:244px;height:307px;background:linear-gradient(160deg,#8d8d8d,#c7c2b8)" role="img" aria-label="Project photo of white gravel grid">
  <div class="tile-overlay">
    <svg width="36" height="36" viewBox="0 0 36 36" style="margin-bottom:16px"><circle cx="15" cy="15" r="11" fill="none" stroke="#fff" stroke-width="2.4"/><path d="M23 23l10 10M15 10v10M10 15h10" stroke="#fff" stroke-width="2.4"/></svg>
    Pondermesh<br>Pro White
  </div>
</div>
<div class="abs tile" style="left:351px;top:2042px;width:498px;height:146px;background:linear-gradient(180deg,#7a9c55,#4c4c4c)" role="img" aria-label="Curved grid path beside a lawn"></div>
<div class="abs tile" style="left:351px;top:2194px;width:247px;height:155px;background:linear-gradient(160deg,#c9c6c0,#3b3b3b)" role="img" aria-label="Black grid laid at a house front"></div>
<div class="abs tile" style="left:605px;top:2194px;width:244px;height:155px;background:linear-gradient(180deg,#6a8a3a,#3d8c55)" role="img" aria-label="Green grid panels on a site"></div>
<div class="abs tile" style="left:858px;top:2042px;width:242px;height:307px;background:linear-gradient(180deg,#7fa7d8 0%,#9a7f6a 45%,#d7d0c4 100%)" role="img" aria-label="Gravel driveway in front of a house"></div>

<!-- footer -->
<footer class="abs footer">
  <div class="abs" style="left:99px;top:40px">
    <h4>Quick Links</h4>
    <ul class="quick-links"><li>Home</li><li>About Us</li><li>Ground Solutions</li><li>Pondermesh</li><li>Contact Us</li></ul>
  </div>
  <div class="abs" style="left:284px;top:40px;width:300px">
    <h4>Contact Details</h4>
    <div class="contact-line"><svg width="10" height="14" viewBox="0 0 10 14"><path d="M5 13S1 8 1 5a4 4 0 018 0c0 3-4 8-4 8z" fill="var(--green)"/><circle cx="5" cy="5" r="1.5" fill="#fff"/></svg><div>PONDERMESH ECO SOLUTIONS LTD<br>Harlow House, Riverside Ind Est,<br>Dunmore, G00 1AB.</div></div>
    <div class="contact-line"><svg width="11" height="11" viewBox="0 0 11 11"><path d="M1 2l2.5-1 1.5 3-1.5 1c.8 1.6 1.6 2.4 3 3l1-1.5 3 1.5-1 2.5C4.5 10.5.5 6.5 1 2z" fill="var(--green)"/></svg><div>0131-555-0182</div></div>
    <div class="contact-line"><svg width="11" height="11" viewBox="0 0 11 11"><path d="M1 2l2.5-1 1.5 3-1.5 1c.8 1.6 1.6 2.4 3 3l1-1.5 3 1.5-1 2.5C4.5 10.5.5 6.5 1 2z" fill="var(--green)"/></svg><div>0845-555-0145</div></div>
    <div class="contact-line"><svg width="12" height="10" viewBox="0 0 12 10"><rect x="0.5" y="0.5" width="11" height="9" fill="var(--green)"/><path d="M1 1l5 4 5-4" fill="none" stroke="#fff"/></svg><div>sales@pondermeshpaths.co.uk</div></div>
  </div>
  <div class="abs" style="left:600px;top:40px">
    <h4>Location Map</h4>
    <div class="map" role="img" aria-label="Street map showing the office location"></div>
  </div>
  <div class="abs" style="left:905px;top:68px">
    <div class="footer-brand"><div class="brand-mark"></div><div>PONDERMESH<span>GROUND SOLUTIONS</span></div></div>
    <div class="social" style="margin:22px 0 0 36px"><i></i><i></i><i></i><i></i></div>
  </div>
</footer>
<div class="abs copyright">Copyright © 2016 Pondermesh Eco Solutions Ltd. All Rights Reserved.</div>
<div class="abs pay" style="left:911px"></div>
<div class="abs pay" style="left:959px"></div>
<div class="abs pay" style="left:1007px"></div>
<div class="abs pay" style="left:1055px"></div>

</body>
</html>
```